Specialised investor in e-mobility and energy wants business card design

We need a business card design that fits our existing corporate design. <The look and feel must be 'sharp'/'clean', dynamic, communicate momentum, professionalism etc (as one would imagine from a firm in the financial sector). We like the idea of a reverse-side of the card that includes the logo, and the name and contact details on the other. We expect the deliverable to be whatever format might be required to be able to get cards printed directly by a service such as kelmo press. Our website is www.zub.capital

```html
<!DOCTYPE html>
<html lang="en">
<head>
<meta charset="utf-8">
<title>Zub capital business card</title>
<link href="https://fonts.googleapis.com/css2?family=Montserrat:wght@400;500;700&display=swap" rel="stylesheet">
<style>
  :root {
    --backdrop: #2e2e2e;
    --brand-green: #8ab34c;
    --brand-dark: #2f4f1f;
    --card-white: #ffffff;
    --ink: #1c1c1c;
    --card-shadow: rgba(0, 0, 0, 0.45);
  }
  * { box-sizing: border-box; margin: 0; padding: 0; }
  html, body {
    width: 1200px; height: 689px; overflow: hidden;
    background: var(--backdrop);
    font-family: "Montserrat", sans-serif;
  }
  .canvas {
    position: relative; width: 1200px; height: 689px;
    display: flex; align-items: center; justify-content: center; gap: 48px;
  }
  .card {
    position: relative; width: 540px; height: 318px;
    border-radius: 22px;
    box-shadow: 0 18px 40px var(--card-shadow);
    overflow: hidden;
  }
  .card--front { background: var(--brand-green); }
  .card--back { background: var(--card-white); }

  .wordmark {
    display: flex; align-items: center; gap: 14px;
    font-weight: 500; color: var(--brand-dark);
    letter-spacing: 0.5px; white-space: nowrap;
  }
  .wordmark__dot {
    border-radius: 50%; background: var(--brand-dark); flex: none;
  }
  .card--front .wordmark {
    position: absolute; left: 50%; top: 50%;
    transform: translate(-50%, -50%);
    font-size: 64px;
  }
  .card--front .wordmark__dot { width: 34px; height: 34px; }

  .card--back .wordmark {
    position: absolute; right: 34px; top: 30px;
    font-size: 38px; gap: 10px;
  }
  .card--back .wordmark__dot { width: 22px; height: 22px; }

  .person { position: absolute; left: 34px; top: 150px; }
  .person__name {
    font-weight: 700; font-size: 17px; color: var(--brand-green);
    text-transform: uppercase; letter-spacing: 0.3px;
  }
  .person__role { font-size: 14px; color: var(--ink); margin-top: 2px; }

  .company {
    position: absolute; right: 34px; top: 150px;
    text-align: right; font-size: 14px; line-height: 1.4; color: var(--ink);
  }

  .contacts {
    position: absolute; left: 34px; bottom: 30px;
    list-style: none; font-size: 14px; color: var(--ink); line-height: 1.55;
  }
  .contacts li { display: flex; align-items: center; gap: 8px; }
  .contacts svg { width: 12px; height: 12px; fill: var(--brand-green); flex: none; }
</style>
</head>
<body>
<main class="canvas">
  <section class="card card--front" aria-label="Card front">
    <div class="wordmark"><span class="wordmark__dot"></span>Zub capital</div>
  </section>

  <section class="card card--back" aria-label="Card back">
    <div class="wordmark"><span class="wordmark__dot"></span>Zub capital</div>

    <div class="person">
      <p class="person__name">Lukas Fernau</p>
      <p class="person__role">team directly</p>
    </div>

    <address class="company" style="font-style: normal;">
      Zub Capital S.A.<br>Geneva, Switzerland
    </address>

    <ul class="contacts">
      <li>
        <svg viewBox="0 0 12 12" aria-hidden="true"><path d="M2.4 0.6 4.2 2.8 3.2 4.2C3.9 5.9 6.1 8.1 7.8 8.8L9.2 7.8 11.4 9.6 10.2 11.4C5.4 11.2 0.8 6.6 0.6 1.8Z"/></svg>
        +41 70555 0184
      </li>
      <li>
        <svg viewBox="0 0 12 12" aria-hidden="true"><path d="M0.5 2.5H11.5V9.5H0.5Z M1 3 6 7 11 3" stroke="#fff" stroke-width="0.8"/></svg>
        lukas@zub.capital
      </li>
      <li>
        <svg viewBox="0 0 12 12" aria-hidden="true"><circle cx="6" cy="6" r="5.5"/><path d="M0.5 6H11.5M6 0.5C3.5 3.5 3.5 8.5 6 11.5M6 0.5C8.5 3.5 8.5 8.5 6 11.5" stroke="#fff" stroke-width="0.7" fill="none"/></svg>
        www.zub.capital
      </li>
    </ul>
  </section>
</main>
</body>
</html>
```